Letterhead, stationery and email signature for construction business

I need the letterhead, stationery and email signature designs for a construction business. I want them to have a corporate feel to them.

I've attached the logo for reference.

```html
<!DOCTYPE html>
<html lang="en">
<head>
<meta charset="utf-8">
<title>Norvale Projects Letterhead</title>
<link rel="stylesheet" href="https://fonts.googleapis.com/css2?family=Lato:wght@400;700;900&family=Manrope:wght@700&family=Tangerine:wght@700&display=swap">
<style>
  :root {
    --backdrop: #e4e4e4;
    --brand-blue: #2d56a0;
    --rule-grey: #5a5b64;
    --ink: #2f2f33;
    --ink-strong: #26262a;
  }
  * { box-sizing: border-box; margin: 0; padding: 0; }
  html, body { width: 1153px; height: 1200px; overflow: hidden; }
  body {
    background: var(--backdrop);
    font-family: "Lato", Arial, sans-serif;
    color: var(--ink);
    position: relative;
  }
  .letterhead {
    position: absolute;
    left: 170px; top: 30px;
    width: 814px; height: 1140px;
    background: radial-gradient(ellipse at 55% 35%, #ffffff 0%, #f9f9f9 40%, #f1f1f1 100%);
    overflow: hidden;
  }
  .brand {
    position: absolute; left: 74px; top: 82px;
    display: flex; align-items: center; gap: 12px;
  }
  .brand-square { width: 44px; height: 44px; background: var(--brand-blue); }
  .brand-name {
    font-family: "Lato", Arial, sans-serif;
    font-weight: 900;
    font-size: 23px;
    letter-spacing: 1px;
    color: var(--brand-blue);
    line-height: 1;
  }
  .contact {
    position: absolute; left: 554px; top: 50px;
    border-left: 1.5px solid var(--brand-blue);
    padding-left: 7px;
    font-family: "Manrope", Arial, sans-serif;
    font-style: normal;
    font-weight: 700;
    font-size: 12.5px;
    color: var(--ink-strong);
    line-height: 1.4;
  }
  .contact-address { margin-bottom: 8px; }
  .contact-line { display: flex; align-items: center; gap: 6px; }
  .contact-line svg { width: 12px; height: 12px; fill: var(--brand-blue); flex: none; }
  .letter {
    position: absolute; left: 63px; top: 252px; width: 689px;
    font-size: 15px; line-height: 1.17;
  }
  .letter-date { margin-bottom: 20px; }
  .letter-recipient { margin-bottom: 18px; }
  .letter-company { margin-bottom: 24px; }
  .letter-salutation { font-size: 18px; font-weight: 700; margin-bottom: 20px; }
  .letter-body p { text-align: justify; margin-bottom: 17px; }
  .letter-closing { margin-top: 36px; }
  .letter-signature {
    font-family: "Tangerine", "Brush Script MT", cursive;
    font-weight: 700;
    font-size: 46px;
    color: var(--ink-strong);
    margin-top: 16px;
    margin-left: 4px;
  }
  .footer-rule {
    position: absolute; left: 0; right: 0; bottom: 96px;
    height: 3px; background: var(--rule-grey);
  }
  .footer-band {
    position: absolute; left: 0; right: 0; bottom: 0;
    height: 88px; background: var(--brand-blue);
  }
</style>
</head>
<body>
  <main class="letterhead">
    <header>
      <div class="brand">
        <span class="brand-square"></span>
        <span class="brand-name">NORVALE PROJECTS</span>
      </div>
      <address class="contact">
        <div class="contact-address">42-07 Larch St 12,<br>Ridgeview, NY 11402</div>
        <div class="contact-line">
          <svg viewBox="0 0 24 24"><path d="M3 9c0-3 4-5 9-5s9 2 9 5v2h-5V9H8v2H3zM6 12h12l2 8H4z"/></svg>
          555-201-4830
        </div>
        <div class="contact-line">
          <svg viewBox="0 0 24 24"><path d="M2 5h20v14H2zm2 2v.5l8 5.5 8-5.5V7l-8 5.5z"/></svg>
          info@norvaleprojects.com
        </div>
        <div class="contact-line">
          <svg viewBox="0 0 24 24"><circle cx="12" cy="12" r="10"/></svg>
          www.norvaleprojects.com
        </div>
      </address>
    </header>

    <article class="letter">
      <p class="letter-date">Feb-03-2022</p>
      <p class="letter-recipient">Mr, John Doe<br>President</p>
      <p class="letter-company">Harbor Group<br>123 Street Name, Suite# 10<br>City, State, 120023</p>
      <p class="letter-salutation">Dear Mr, John</p>
      <div class="letter-body">
        <p>Lorem ipsum dolor sit amet, consectetur adipisicing elit, sed do eiusmod tempor incididunt ut labore et dolore magna aliqua. Ut enim ad minim veniam, quis nostrud exercitation ullamco laboris nisi ut aliquip ex ea commodo consequat. Duis aute irure dolor in reprehenderit in voluptate velit esse cillum dolore eu fugiat nulla pariatur.</p>
        <p>Lorem ipsum dolor sit amet, consectetur adipisicing elit, sed do eiusmod tempor incididunt ut labore et dolore magna aliqua. Ut enim ad minim veniam, quis nostrud exercitation ullamco laboris nisi ut aliquip ex ea commodo consequat. Duis aute irure dolor in reprehenderit in voluptate velit esse cillum dolore eu fugiat nulla pariatur.</p>
        <p>Lorem ipsum dolor sit amet, consectetur adipisicing elit, sed do eiusmod tempor incididunt ut labore et dolore magna aliqua. Ut enim ad minim veniam, quis nostrud exercitation ullamco laboris nisi ut aliquip ex ea commodo consequat.</p>
        <p>Excepteur sint occaecat cupidatat non proident, sunt in culpa qui officia deserunt mollit anim id est laborum. re et dolore magnam aliquam quaerat voluptatem.</p>
      </div>
      <p class="letter-closing">Regards</p>
      <p class="letter-signature">Daniel Ward</p>
    </article>

    <footer>
      <div class="footer-rule"></div>
      <div class="footer-band"></div>
    </footer>
  </main>
</body>
</html>
```